Calder Vossik - Cinematographer

NEED:
I'm looking for a sleek, professional, modern business card that will give give the recipient the impression that they can trust their production will go smoothly by hiring me. I will bring creativity and knowledge to their shoot, so that we can create powerful images.
I am looking for a card with a strong style and design ethos that could be expanded to a website and a full visual/graphic/design entity for me.
ABOUT ME:
I am a mid-twenties cinematographer, I work on music video, narrative short, commercial, and corporate projects. I blend the science and artistry of cameras and filmmaking to tell a story. I'm an artist, a technician, and a manager.
DESIGN:
I like sleek, simple design. Black, dark grays, white, dark navy, steel blues, I love cyan, but also cyan and red. I am not a fan of earthy tones. I generally prefer modern, san-serif fonts over serifs. My old logo was based on an aperture, a multi-blade device at the back of a lens that controls how much light passes through, but I made it with so many colors, that it doesn't necessarily lend itself to a specific color-scheme or design ethos. I liked that the aperture design provided a sense of the technical requirements of my job. I'm a fan of matte business cards, but am open to plenty of specialty print processes to make an outstanding card.
ATTACHED FILES:
My Old Rainbox Aperture Logo, plus a few designs I've tried playing around with, but am not tied to. I AM OPEN TO NEW DESIGNS, DO NOT FEEL TIED TO THIS.
**I've pulled my old logo down from the attached files, and instead attached other business cards I like, so as not to mislead you where I would like to go.
INFO:
Name: Calder Vossik
Job: Cinematographer
Email: ccvossik@lumenpost.net
Phone: 415.555.0193
Website: caldervossik.com
Updates
I'm adding some images of other cards that I like, and removing my old logo, since I'm looking for something new, and don't want that old logo to push anyone a certain direction.

```html
<!DOCTYPE html>
<html lang="en">
<head>
<meta charset="utf-8">
<title>Calder Vossik – Cinematographer Business Card</title>
<link href="https://fonts.googleapis.com/css2?family=Lato:wght@400;700;900&display=swap" rel="stylesheet">
<style>
  :root {
    --page-bg: #e4e4e4;
    --card-white: #ffffff;
    --card-black: #120a0a;
    --ink: #111111;
    --ink-soft: #2a2a2a;
    --accent-red: #ea4b3c;
    --tile-black: #0c0606;
  }
  * { box-sizing: border-box; margin: 0; padding: 0; }
  html, body {
    width: 1200px; height: 926px; overflow: hidden;
    background: var(--page-bg);
    font-family: "Lato", "Helvetica Neue", Arial, sans-serif;
  }
  .sheet { position: relative; width: 1200px; height: 926px; }

  .card {
    position: absolute; left: 230px; width: 740px; height: 423px;
    box-shadow: 0 6px 18px rgba(0,0,0,0.18);
  }
  .card--front { top: 30px; background: var(--card-white); }
  .card--back  { top: 473px; background: var(--card-black); }

  /* Front */
  .frame-strip {
    position: absolute; left: 30px; top: 28px;
    display: flex; flex-direction: column; gap: 9px;
  }
  .frame-strip__cell {
    width: 48px; height: 48px; border-radius: 6px; background: var(--tile-black);
  }
  .identity {
    position: absolute; left: 92px; top: 28px;
    display: flex; align-items: center; gap: 14px;
  }
  .identity__mark {
    width: 92px; height: 92px; border-radius: 8px; background: var(--accent-red);
  }
  .identity__text { display: flex; flex-direction: column; align-items: flex-end; margin-top: 18px; }
  .identity__name {
    font-weight: 700; font-size: 46px; letter-spacing: -1px; color: var(--ink); line-height: 1;
  }
  .identity__role {
    font-weight: 900; font-size: 11px; letter-spacing: 1px; color: var(--ink); margin-top: 4px;
  }

  .contact {
    position: absolute; right: 34px; bottom: 40px;
    list-style: none; display: flex; flex-direction: column; gap: 6px;
  }
  .contact__item {
    display: flex; align-items: center; justify-content: flex-end; gap: 18px;
    font-size: 22px; color: var(--ink-soft); line-height: 1.15;
  }
  .contact__icon { width: 22px; height: 22px; flex: none; }

  /* Back */
  .signature {
    position: absolute; right: 60px; bottom: 80px;
    display: flex; align-items: center; gap: 16px;
  }
  .signature__mark { width: 44px; height: 44px; border-radius: 4px; background: var(--accent-red); }
  .signature__name {
    font-weight: 700; font-size: 30px; letter-spacing: 9px; color: var(--card-white);
  }
</style>
</head>
<body>
<main class="sheet">

  <section class="card card--front" aria-label="Business card front">
    <div class="frame-strip" aria-hidden="true">
      <span class="frame-strip__cell"></span>
      <span class="frame-strip__cell"></span>
      <span class="frame-strip__cell"></span>
      <span class="frame-strip__cell"></span>
      <span class="frame-strip__cell"></span>
      <span class="frame-strip__cell"></span>
    </div>

    <div class="identity">
      <span class="identity__mark" aria-hidden="true"></span>
      <div class="identity__text">
        <h1 class="identity__name">Calder Vossik</h1>
        <p class="identity__role">CINEMATOGRAPHER</p>
      </div>
    </div>

    <ul class="contact">
      <li class="contact__item">415.555.0193
        <svg class="contact__icon" viewBox="0 0 22 22" aria-hidden="true">
          <rect x="6" y="2" width="10" height="18" rx="1.5" fill="none" stroke="#555" stroke-width="1.6"/>
          <line x1="7" y1="15.5" x2="15" y2="15.5" stroke="#555" stroke-width="1.2"/>
        </svg>
      </li>
      <li class="contact__item">ccvossik@lumenpost.net
        <svg class="contact__icon" viewBox="0 0 22 22" aria-hidden="true">
          <rect x="2" y="5" width="18" height="12" fill="#555"/>
          <polyline points="2,5 11,12 20,5" fill="none" stroke="#fff" stroke-width="1.3"/>
        </svg>
      </li>
      <li class="contact__item">www.caldervossik.com
        <svg class="contact__icon" viewBox="0 0 22 22" aria-hidden="true">
          <circle cx="11" cy="11" r="8" fill="none" stroke="#555" stroke-width="1.6"/>
          <ellipse cx="11" cy="11" rx="3.5" ry="8" fill="none" stroke="#555" stroke-width="1.2"/>
          <line x1="3" y1="11" x2="19" y2="11" stroke="#555" stroke-width="1.2"/>
        </svg>
      </li>
    </ul>
  </section>

  <section class="card card--back" aria-label="Business card back">
    <div class="signature">
      <span class="signature__mark" aria-hidden="true"></span>
      <p class="signature__name">CALDER VOSSIK</p>
    </div>
  </section>

</main>
</body>
</html>
```